Business Card Design Project - 2 sided

We need a business card design for a card having one business on each side (ie. two businesses on one card). Would like a design that incorporates logo, tagline and normal fields (name, position, address, phone).

Would also like an allowance for small font text along the bottom (text to be determined, but less than 50 characters).

NB. Attached logo for Harbor Quill has two variations - either can be used.

www.harborquill-example.com / www.velmaro-example.com

```html
<!DOCTYPE html>
<html lang="en">
<head>
<meta charset="utf-8">
<title>Harbor Quill / Velmaro – Business Card</title>
<link rel="stylesheet" href="https://fonts.googleapis.com/css2?family=Source+Sans+3:wght@400;600;700&display=swap">
<style>
  :root {
    --backdrop: #ebe8e4;
    --card: #ffffff;
    --green: #8dc63f;
    --green-band: #8cc541;
    --navy: #2e3370;
    --ink: #555555;
    --rule: #9a9a9a;
    --white: #ffffff;
  }
  * { box-sizing: border-box; margin: 0; padding: 0; }
  html, body {
    width: 1200px; height: 487px; overflow: hidden;
    background: var(--backdrop);
    font-family: "Source Sans 3", Arial, sans-serif;
  }
  .canvas { position: relative; width: 1200px; height: 487px; }
  .card {
    position: absolute; top: 89px; width: 543px; height: 309px;
    background: var(--card); border-radius: 14px; overflow: hidden;
    box-shadow: 0 2px 6px rgba(0,0,0,0.18);
  }
  .card--front { left: 44px; }
  .card--back { left: 612px; }

  .brand { position: absolute; left: 34px; }
  .card--front .brand { top: 98px; }
  .card--back .brand { top: 68px; left: 36px; }
  .brand__name {
    font-weight: 600; font-size: 28px; letter-spacing: 1px; line-height: 1;
    color: var(--navy);
  }
  .brand__tagline { font-size: 11.5px; color: var(--ink); margin-top: 8px; }
  .card--back .brand__tagline { letter-spacing: 0.5px; font-size: 12px; }

  .person {
    position: absolute; left: 33px; top: 180px;
    font-size: 18px; color: var(--green); font-weight: 700;
  }
  .person__title { font-weight: 400; font-size: 14px; color: var(--ink); }
  .person__slash { font-weight: 400; color: #999; font-size: 15px; margin: 0 3px; }

  .rule { position: absolute; left: 0; right: 0; top: 214px; height: 3px; background: var(--rule); }
  .band {
    position: absolute; left: 0; right: 0; top: 220px; bottom: 0;
    background: var(--green-band); color: var(--white);
  }
  .contacts { position: absolute; top: 9px; left: 32px; display: flex; font-size: 14px; line-height: 18px; }
  .contacts__col { padding-right: 10px; }
  .contacts__col + .contacts__col { border-left: 1px solid rgba(255,255,255,0.75); padding-left: 10px; }
  .contacts__col--phone { width: 114px; }
  .contacts__col--web { width: 160px; }
  .contacts__item { display: flex; align-items: center; gap: 6px; white-space: nowrap; }
  .icon { width: 10px; height: 10px; flex: none; }
  .footnote { position: absolute; left: 32px; top: 50px; font-size: 11px; letter-spacing: 0.3px; }
</style>
</head>
<body>
<div class="canvas">

  <section class="card card--front">
    <div class="brand">
      <p class="brand__name">Harbor Quill</p>
      <p class="brand__tagline">Website Translation and Localisation Specialist...</p>
    </div>
    <p class="person">YOUR NAME<span class="person__slash">/</span><span class="person__title">Title</span></p>
    <div class="rule"></div>
    <div class="band">
      <div class="contacts">
        <div class="contacts__col contacts__col--phone">
          <p class="contacts__item"><svg class="icon" viewBox="0 0 10 10"><path d="M2 0.5 L4 2.5 L3 4 Q4.5 6 6 7 L7.5 6 L9.5 8 L8 9.5 Q3 9 0.5 2 Z" fill="#fff"/></svg>123-456-7890</p>
          <p class="contacts__item"><svg class="icon" viewBox="0 0 10 10"><rect x="2" y="0" width="6" height="10" rx="1" fill="#fff"/><rect x="3" y="1.5" width="4" height="5" fill="#8cc541"/></svg>123-456-7890</p>
        </div>
        <div class="contacts__col contacts__col--web">
          <p class="contacts__item"><svg class="icon" viewBox="0 0 10 10"><rect x="0" y="2" width="10" height="7" fill="#fff"/><path d="M0 2 L5 6 L10 2" stroke="#8cc541" fill="none"/></svg>name@website.com</p>
          <p class="contacts__item"><svg class="icon" viewBox="0 0 10 10"><circle cx="5" cy="5" r="4.5" fill="#fff"/></svg>www.website.com</p>
        </div>
        <div class="contacts__col">
          <p>Complex name, Street</p>
          <p>City, State, zip code</p>
        </div>
      </div>
      <p class="footnote">xxxxxxxxxxxxxxxxxxxxxxxxxxxxxxxxxxxxxxxxxxxxxxxxxx</p>
    </div>
  </section>

  <section class="card card--back">
    <div class="brand">
      <p class="brand__name">Velmaro</p>
      <p class="brand__tagline">Professional SEO Services</p>
    </div>
    <p class="person">YOUR NAME<span class="person__slash">/</span><span class="person__title">Title</span></p>
    <div class="rule"></div>
    <div class="band">
      <div class="contacts">
        <div class="contacts__col contacts__col--phone">
          <p class="contacts__item"><svg class="icon" viewBox="0 0 10 10"><path d="M2 0.5 L4 2.5 L3 4 Q4.5 6 6 7 L7.5 6 L9.5 8 L8 9.5 Q3 9 0.5 2 Z" fill="#fff"/></svg>123-456-7890</p>
          <p class="contacts__item"><svg class="icon" viewBox="0 0 10 10"><rect x="2" y="0" width="6" height="10" rx="1" fill="#fff"/><rect x="3" y="1.5" width="4" height="5" fill="#8cc541"/></svg>123-456-7890</p>
        </div>
        <div class="contacts__col contacts__col--web">
          <p class="contacts__item"><svg class="icon" viewBox="0 0 10 10"><rect x="0" y="2" width="10" height="7" fill="#fff"/><path d="M0 2 L5 6 L10 2" stroke="#8cc541" fill="none"/></svg>name@website.com</p>
          <p class="contacts__item"><svg class="icon" viewBox="0 0 10 10"><circle cx="5" cy="5" r="4.5" fill="#fff"/></svg>www.website.com</p>
        </div>
        <div class="contacts__col">
          <p>Complex name, Street</p>
          <p>City, State, zip code</p>
        </div>
      </div>
      <p class="footnote">xxxxxxxxxxxxxxxxxxxxxxxxxxxxxxxxxxxxxxxxxxxxxxxxxx</p>
    </div>
  </section>

</div>
</body>
</html>
```